The design should look similar to the uploaded example to accommodate the information needed for a business card template. I would like to see the colors orange and charcoal grey incorporated along with the logo.The following should be on the back of the card SPECIALIZING IN NEW AND USED TIRES & WHEELS FOR:- Loaders- Skid Steers- Telehandlers- Boom Lifts- Forklifs and moreELIMINATING DOWNTIMEWheel Exchange Program for New & Used Foam Filled and Solid Rubber TiresSPECIALTY SERVICES- Foam Filling Tires- Largest Tire Press in SE- ONSITE Forklift Tire Press- Boom Truck Services - Rubber Tracks

Target Market(s)

New and Existing Customers

Industry/Entity Type

Business

Contact Information for Business Card

NAMEHEAVY DUTY TIRE, LLC8470 Belvedere RoadWest Palm Beach, FL 33411P: 844-GRANITE RIM-TIRESF: 561-431-6469C:E: W: WWW.GRANITERIMSUPPLY-EXAMPLE.COM

Font styles to use
Sans Serif

Colors
f37122
333333

Requirements
Must have
• The logo and the information indicated for the backside of the card
Nice to have
• Keep the orange and charcoal grey colors

```html
<!DOCTYPE html>
<html lang="en">
<head>
<meta charset="utf-8">
<title>Granite Rim Supply, LLC – Business Card</title>
<link rel="stylesheet" href="https://fonts.googleapis.com/css2?family=Alfa+Slab+One&family=Open+Sans:wght@400;700&family=Tinos:wght@400;700&display=swap">
<style>
  :root {
    --orange: #f58a45;
    --charcoal: #3a4444;
    --ink: #1e1e1e;
    --white: #ffffff;
    --violet: #5a3fa8;
    --stage: #000000;
  }
  html, body {
    margin: 0;
    width: 1200px;
    height: 927px;
    overflow: hidden;
    background: var(--stage);
  }
  .canvas { position: relative; width: 1200px; height: 927px; }
  .card {
    position: absolute;
    left: 367px;
    width: 435px;
    height: 268px;
    overflow: hidden;
  }
  .card svg.card-shapes { position: absolute; inset: 0; }
  .card-front { top: 132px; background: var(--orange); }
  .card-back { top: 481px; background: var(--white); }

  .brand-name {
    position: absolute; right: 40px; top: 44px; margin: 0;
    font: 400 21px/1 "Alfa Slab One", serif;
    color: var(--charcoal); letter-spacing: 0.5px; white-space: nowrap;
  }
  .brand-mark {
    position: absolute; left: 28px; top: 100px; width: 116px; text-align: center;
  }
  .brand-mark .dot {
    display: block; width: 72px; height: 72px; margin: 0 auto 6px;
    border-radius: 50%; background: var(--charcoal);
  }
  .brand-mark .label {
    font: 700 12px/1.1 "Open Sans", sans-serif; color: var(--charcoal);
  }
  .contact {
    position: absolute; right: 42px; top: 93px; margin: 0;
    text-align: right; font-family: "Open Sans", sans-serif; font-style: normal;
    white-space: nowrap;
  }
  .contact .address { color: var(--white); font-size: 15px; line-height: 18px; }
  .contact .phone { color: var(--violet); font-size: 19px; line-height: 24px; margin-top: 4px; }
  .contact .fax { color: var(--white); font-size: 19px; line-height: 23px; }
  .contact .web { color: var(--ink); font-size: 15px; line-height: 20px; }

  .back-text { position: absolute; font-family: "Tinos", serif; color: var(--ink); font-size: 10px; line-height: 16.5px; }
  .back-text h2 { font-size: 10.5px; font-weight: 700; line-height: 12.5px; margin: 0 0 6px; }
  .back-text ul { list-style: none; margin: 0; padding: 0; }
  .specialties { left: 39px; top: 82px; }
  .services { right: 34px; top: 80px; text-align: right; }
  .services .group-title { text-transform: uppercase; }
  .faint-mark {
    position: absolute; left: 173px; top: 183px; width: 162px; height: 162px;
    border-radius: 50%; background: rgba(120,120,120,0.22);
  }
  .faint-mark span {
    position: absolute; left: 0; right: 0; top: 40px; text-align: center;
    font: 700 15px/1 "Open Sans", sans-serif; color: rgba(255,255,255,0.55);
  }
</style>
</head>
<body>
<div class="canvas">

  <section class="card card-front" aria-label="Card front">
    <svg class="card-shapes" width="435" height="268" viewBox="0 0 435 268" aria-hidden="true">
      <polygon points="0,220 138,208 435,268 0,268" fill="var(--charcoal)"/>
      <polygon points="0,228 136,217 400,268 0,268" fill="var(--white)"/>
    </svg>
    <h1 class="brand-name">GRANITE RIM SUPPLY LLC</h1>
    <div class="brand-mark">
      <span class="dot"></span>
      <span class="label">GRANITE RIM</span>
    </div>
    <address class="contact">
      <div class="address">5126 Marston Lane<br>Harbor Pines, FL 33480</div>
      <div class="phone">P: 844-GR-WHEEL</div>
      <div class="fax">F: 561-278-9053</div>
      <div class="web">www.graniterimsupply-example.com</div>
    </address>
  </section>

  <section class="card card-back" aria-label="Card back">
    <svg class="card-shapes" width="435" height="268" viewBox="0 0 435 268" aria-hidden="true">
      <polygon points="135,0 435,0 435,268 280,268" fill="var(--orange)"/>
    </svg>
    <div class="faint-mark"><span>GRANITE RIM</span></div>
    <div class="back-text specialties">
      <h2>specializing in new and<br>used tires &amp; wheels for:</h2>
      <ul>
        <li>Loaders</li>
        <li>Skid Steers</li>
        <li>Telehandlers</li>
        <li>Boom Lifts</li>
        <li>Forklifs and more</li>
      </ul>
    </div>
    <div class="back-text services">
      <h2>Wheel Exchange Program for New &amp;<br>Used Foam Filled and Solid Rubber Tires</h2>
      <ul>
        <li class="group-title">Specialty Services</li>
        <li>Foam Filling Tires</li>
        <li>Largest Tire Press in SE</li>
        <li>ONSITE Forklift Tire Press</li>
        <li>Boom Truck Services</li>
        <li>Rubber Tracks</li>
      </ul>
    </div>
  </section>

</div>
</body>
</html>
```